New Business Card Design Project

Use the flyer uploaded and website www.brightoakbuilders.com for inspiration.
List Our Services on Backside of business cards
Marcus Delling
Harborline Builders Inc.
Licensed General Contractors
858-471-6093

Contact Information for Business Card

Use the flyer uploaded and website www.brightoakbuilders.com for inspiration. List Our Services on Backside of business cards Marcus Delling Harborline Builders Inc. Licensed General Contractors 858-471-6093

```html
<!DOCTYPE html>
<html lang="en">
<head>
<meta charset="utf-8">
<title>Harborline Builders – Business Card</title>
<link rel="stylesheet" href="https://fonts.googleapis.com/css2?family=Montserrat:wght@400;500;700&display=swap">
<style>
  :root {
    --page-bg: #1b1b1b;
    --card-bg: #262626;
    --card-edge: #2f2f2f;
    --text-main: #f2f2f2;
    --text-soft: #d4d4d4;
    --art-light: #5a5a5a;
    --art-dark: #2c2c2c;
  }
  * { margin: 0; padding: 0; box-sizing: border-box; }
  html, body { width: 1200px; height: 875px; overflow: hidden; }
  body {
    background: var(--page-bg);
    font-family: "Montserrat", sans-serif;
    color: var(--text-main);
    position: relative;
  }
  .card {
    position: absolute;
    top: 283px;
    width: 540px;
    height: 309px;
    background: var(--card-bg);
    border: 1px solid var(--card-edge);
    border-radius: 16px;
    overflow: hidden;
    box-shadow: 0 18px 40px rgba(0,0,0,0.55);
  }
  .card--back { left: 40px; }
  .card--front { left: 620px; }

  .brand-name {
    font-weight: 400;
    font-size: 16px;
    letter-spacing: 1.5px;
    text-transform: uppercase;
    color: var(--text-main);
    white-space: nowrap;
  }

  /* back side */
  .back-art {
    position: absolute;
    left: 0; top: 0;
    width: 250px; height: 309px;
    background: radial-gradient(ellipse at 40% 30%, var(--art-light) 0%, var(--art-dark) 70%);
  }
  .card--back .brand-name {
    position: absolute;
    left: 272px; top: 38px;
  }
  .services {
    position: absolute;
    left: 272px; top: 78px;
    width: 250px;
  }
  .services__title {
    font-weight: 700;
    font-size: 15px;
    padding-bottom: 5px;
    border-bottom: 1px solid var(--text-soft);
    width: 130px;
    margin-bottom: 8px;
  }
  .services__list { list-style: none; }
  .services__list li {
    font-size: 11.5px;
    line-height: 19px;
    color: var(--text-soft);
    padding-left: 14px;
    position: relative;
  }
  .services__list li::before {
    content: "";
    position: absolute;
    left: 2px; top: 8px;
    width: 4px; height: 4px;
    border-radius: 50%;
    background: var(--text-soft);
  }

  /* front side */
  .card--front .brand-name {
    position: absolute;
    left: 36px; top: 120px;
  }
  .front-art {
    position: absolute;
    right: 24px; top: 70px;
    width: 200px; height: 239px;
    background: linear-gradient(160deg, #4a4a4a 0%, #2a2a2a 75%);
    border-radius: 4px 4px 0 0;
  }
  .person {
    position: absolute;
    right: 30px; top: 22px;
    text-align: right;
  }
  .person__name { font-weight: 700; font-size: 19px; }
  .person__role { font-size: 11px; color: var(--text-soft); }
  .license {
    position: absolute;
    left: 36px; top: 190px;
    font-size: 12px;
    color: var(--text-soft);
  }
  .contacts {
    position: absolute;
    left: 36px; top: 224px;
    list-style: none;
  }
  .contacts li {
    display: flex;
    align-items: center;
    gap: 9px;
    font-size: 12px;
    line-height: 21px;
    color: var(--text-soft);
  }
  .contacts svg { width: 12px; height: 12px; fill: var(--text-main); flex: none; }
</style>
</head>
<body>

<section class="card card--back" aria-label="Business card back">
  <div class="back-art" role="img" aria-label="Faint gloss illustration of a palm tree over a house outline"></div>
  <div class="brand-name">Harborline Builders</div>
  <div class="services">
    <h2 class="services__title">Our Services</h2>
    <ul class="services__list">
      <li>Remodel: Kitchen &amp; Bath</li>
      <li>Painting: Interior &amp; Exterior</li>
      <li>Flooring: Carpet, Vinyl, Wood</li>
      <li>Window: Door Replacement</li>
      <li>Plumbing: Repair &amp; Upgrades</li>
      <li>Energy Efficient Upgrades</li>
      <li>Deck &amp; Patio Construction</li>
      <li>Water &amp; Mold Damage</li>
      <li>Garage Renovation</li>
    </ul>
  </div>
</section>

<section class="card card--front" aria-label="Business card front">
  <div class="front-art" role="img" aria-label="Line illustration of a palm tree rising behind a house outline"></div>
  <div class="person">
    <div class="person__name">Marcus Delling</div>
    <div class="person__role">Managing Director</div>
  </div>
  <div class="brand-name">Harborline Builders</div>
  <div class="license">CSLB Licensed No. #1048265</div>
  <ul class="contacts">
    <li>
      <svg viewBox="0 0 24 24" aria-hidden="true"><path d="M6.6 10.8a15.1 15.1 0 0 0 6.6 6.6l2.2-2.2a1 1 0 0 1 1-.25 11.4 11.4 0 0 0 3.6.57 1 1 0 0 1 1 1V20a1 1 0 0 1-1 1A17 17 0 0 1 3 4a1 1 0 0 1 1-1h3.5a1 1 0 0 1 1 1c0 1.25.2 2.45.57 3.57a1 1 0 0 1-.25 1z"/></svg>
      858-471-6093
    </li>
    <li>
      <svg viewBox="0 0 24 24" aria-hidden="true"><path d="M2 5h20v14H2z M3.5 6.5 12 13l8.5-6.5" fill="none" stroke="#f2f2f2" stroke-width="2"/></svg>
      info@brightoakbuilders.com
    </li>
    <li>
      <svg viewBox="0 0 24 24" aria-hidden="true"><circle cx="12" cy="12" r="9" fill="none" stroke="#f2f2f2" stroke-width="2"/><path d="M3 12h18M12 3c3 3 3 15 0 18M12 3c-3 3-3 15 0 18" fill="none" stroke="#f2f2f2" stroke-width="1.5"/></svg>
      www.brightoakbuilders.com
    </li>
  </ul>
</section>

</body>
</html>
```